National Mission Critical Construction Contractor needs Stationery Design to make a bold statement

We are a small commercial construction company, working primarily in mission critical facilities across the U.S.. We have exciting corporate changes going an and a new logo and office space so we need new stationery. The final design should incorporate our new logo and invoke a fresh, high-tech feel while looking simple and modern.

Industry/Entity Type

Construction

Contact Information for Business Card

We are required to list our state licensing qualifications on the back of our card.

Font styles to use
Sans Serif

Requirements
Must have
• We need to have a design for second page of stationery, envelopes both standard and with a window and for a 3 x 4 notepad.

```html
<!DOCTYPE html>
<html lang="en">
<head>
<meta charset="utf-8">
<title>Silver Creek Construction Management – Stationery</title>
<link href="https://fonts.googleapis.com/css2?family=Exo+2:wght@500;600&family=Roboto:wght@400;700&display=swap" rel="stylesheet">
<style>
  :root {
    --bg: #eceeef;
    --paper: #ffffff;
    --blue: #3aaae2;
    --blue-deep: #1f8fd0;
    --blue-pale: #cfe9f8;
    --ink: #3a3a3a;
    --ink-soft: #6b6b6b;
    --grey-curl: #8d9094;
  }
  * { box-sizing: border-box; margin: 0; padding: 0; }
  html, body { width: 1200px; height: 937px; overflow: hidden; }
  body { background: var(--bg); position: relative; font-family: "Roboto", Arial, sans-serif; color: var(--ink); }
  .sheet { position: absolute; background: var(--paper); overflow: hidden; box-shadow: 0 2px 6px rgba(0,0,0,.12); }
  .sheet > svg.art { position: absolute; inset: 0; width: 100%; height: 100%; }

  .brand { position: absolute; display: flex; align-items: center; gap: 6px; font-family: "Exo 2", sans-serif; font-weight: 500; color: var(--blue-deep); line-height: 1.05; text-transform: uppercase; }
  .brand .dot { border: 2px solid var(--blue-deep); border-radius: 50%; flex: none; }
  .brand .name small { display: block; letter-spacing: .18em; }

  /* Letterhead */
  .letterhead { left: 185px; top: 66px; width: 386px; height: 546px; }
  .letterhead .brand { left: 20px; top: 24px; font-size: 19px; }
  .letterhead .brand .dot { width: 30px; height: 30px; }
  .letterhead .brand small { font-size: 6px; margin-top: 2px; }
  .letter { position: absolute; left: 36px; top: 138px; width: 270px; font-size: 5.2px; line-height: 1.55; }
  .letter p { margin-bottom: 7px; }
  .letter .salute { font-weight: 700; margin-bottom: 0; }
  .letter .signature { display: block; width: 40px; height: 16px; background: #e6e6e6; margin: 4px 0 6px; }
  .contact { position: absolute; right: 14px; text-align: right; color: #fff; font-size: 5.2px; line-height: 1.7; }
  .letterhead .contact { top: 452px; }
  .contact .gap { margin-top: 8px; }

  /* Folder */
  .folder { left: 635px; top: 40px; width: 459px; height: 576px; }
  .folder .brand { left: 22px; top: 448px; font-size: 34px; gap: 10px; }
  .folder .brand .dot { width: 60px; height: 60px; border-width: 3px; }
  .folder .brand small { font-size: 11px; margin-top: 4px; letter-spacing: .2em; }
  .folder .web { position: absolute; left: 22px; top: 552px; font-size: 10px; letter-spacing: .22em; font-weight: 700; }

  /* Business cards */
  .card-front { left: 45px; top: 658px; width: 176px; height: 100px; }
  .card-front .person { position: absolute; right: 8px; top: 10px; text-align: right; font-size: 7px; font-weight: 700; }
  .card-front .person span { display: block; font-size: 4px; font-weight: 400; }
  .card-front .contact { color: var(--ink); font-size: 3.6px; top: 40px; right: 8px; line-height: 1.6; }
  .card-front .brand { left: 16px; top: 78px; font-size: 8px; }
  .card-front .brand .dot { width: 13px; height: 13px; border-width: 1.5px; }
  .card-front .brand small { font-size: 3px; }
  .card-back { left: 45px; top: 785px; width: 176px; height: 98px; }
  .card-back .brand { left: 8px; top: 56px; font-size: 11px; }
  .card-back .brand .dot { width: 17px; height: 17px; }
  .card-back .brand small { font-size: 3.6px; }

  /* Envelopes */
  .envelope { left: 265px; top: 672px; width: 432px; height: 208px; }
  .envelope .brand { left: 14px; top: 20px; font-size: 16px; }
  .envelope .brand .dot { width: 24px; height: 24px; }
  .envelope .brand small { font-size: 5px; }
  .envelope-back { left: 737px; top: 672px; width: 431px; height: 208px; }
  .envelope-back .web { position: absolute; left: 0; right: 0; top: 30px; text-align: center; color: #fff; font-size: 10.5px; letter-spacing: .24em; }
</style>
</head>
<body>

<section class="sheet letterhead" aria-label="Letterhead">
  <svg class="art" viewBox="0 0 386 546" preserveAspectRatio="none" aria-hidden="true">
    <path d="M0 520 C140 505 290 470 386 330 L386 360 C300 480 150 515 0 536Z" fill="var(--blue-pale)"/>
    <path d="M0 546 L0 536 C150 520 300 490 386 370 L386 546Z" fill="var(--blue)"/>
  </svg>
  <div class="brand"><span class="dot"></span><span class="name">Silver Creek<small>Construction Management</small></span></div>
  <div class="letter">
    <p>July 2, 2012</p>
    <p class="salute">Dear Sir,</p>
    <p>Harbor Building, Quay St., Westland</p>
    <p>Thank you for the chance to present our work on the new data center. Our team has planned each phase with care so that power, cooling and security stay online while we build. Below is a short outline of the schedule and the people who will lead it on site.</p>
    <p>We will share weekly reports and keep you informed of any change to cost or timing.</p>
    <p>Our field staff hold current licenses in each state where we work, and every crew is trained for live facilities. We look forward to a strong start and to a project that is delivered safely, on time and within budget.</p>
    <p>Best Regards,</p>
    <span class="signature" role="img" aria-label="Handwritten signature"></span>
    <p class="salute">Owen Marsh</p>
    <p>Director<br>Harbor Building, Quay St., Westland</p>
  </div>
  <div class="contact">
    140 Quay Street Level 9<br>Westland
    <div class="gap">555 014 2290 ☏<br>555 014 2291 ☏<br>555 014 2292 ✉</div>
    info@silvercreekcm.com<br>www.silvercreekcm.com
  </div>
</section>

<section class="sheet folder" aria-label="Presentation folder">
  <svg class="art" viewBox="0 0 459 576" preserveAspectRatio="none" aria-hidden="true">
    <defs>
      <linearGradient id="folderGlow" x1="0" y1="0" x2="1" y2="0">
        <stop offset="0" stop-color="var(--blue)" stop-opacity=".55"/>
        <stop offset="1" stop-color="var(--blue)" stop-opacity="0"/>
      </linearGradient>
    </defs>
    <path d="M100 0 L230 0 C280 120 400 260 459 380 L459 576 C430 470 380 380 320 320 C220 230 130 140 100 0Z" fill="url(#folderGlow)"/>
    <path d="M70 0 L102 0 C135 150 250 250 340 330 C400 390 445 480 459 560 L459 576 L448 576 C420 470 370 390 305 330 C200 240 90 140 70 0Z" fill="var(--blue)"/>
  </svg>
  <div class="brand"><span class="dot"></span><span class="name">Silver Creek<small>Construction Management</small></span></div>
  <div class="web">www.silvercreekcm.com</div>
</section>

<section class="sheet card-front" aria-label="Business card front">
  <svg class="art" viewBox="0 0 176 100" preserveAspectRatio="none" aria-hidden="true">
    <path d="M0 0 L60 0 C60 30 40 60 0 80Z" fill="var(--blue)"/>
    <path d="M60 0 L90 0 C80 40 50 70 0 90 L0 80 C40 60 60 30 60 0Z" fill="var(--blue-pale)"/>
  </svg>
  <div class="person">Dana Hollis<span>DIRECTOR</span></div>
  <div class="contact">
    140 Quay Street Level 9<br>Westland<br>
    555 014 2290 ☏<br>555 014 2291 ☏<br>555 014 2292 ✉<br>
    info@silvercreekcm.com<br>www.silvercreekcm.com
  </div>
  <div class="brand"><span class="dot"></span><span class="name">Silver Creek<small>Construction Management</small></span></div>
</section>

<section class="sheet card-back" aria-label="Business card back">
  <svg class="art" viewBox="0 0 176 98" preserveAspectRatio="none" aria-hidden="true">
    <defs>
      <linearGradient id="curlCard" x1="0" y1="0" x2="1" y2="0">
        <stop offset="0" stop-color="var(--grey-curl)"/>
        <stop offset="1" stop-color="#e5e6e7"/>
      </linearGradient>
    </defs>
    <path d="M108 0 L122 0 C128 25 145 40 176 48 L176 56 C140 50 115 30 108 0Z" fill="url(#curlCard)"/>
  </svg>
  <div class="brand"><span class="dot"></span><span class="name">Silver Creek<small>Construction Management</small></span></div>
</section>

<section class="sheet envelope" aria-label="Envelope front">
  <svg class="art" viewBox="0 0 432 208" preserveAspectRatio="none" aria-hidden="true">
    <defs>
      <linearGradient id="curlEnv" x1="0" y1="0" x2="1" y2="0">
        <stop offset="0" stop-color="var(--grey-curl)"/>
        <stop offset="1" stop-color="#e8e9ea"/>
      </linearGradient>
    </defs>
    <path d="M262 0 L290 0 C300 50 350 85 432 95 L432 112 C330 100 275 60 262 0Z" fill="url(#curlEnv)"/>
  </svg>
  <div class="brand"><span class="dot"></span><span class="name">Silver Creek<small>Construction Management</small></span></div>
</section>

<section class="sheet envelope-back" aria-label="Envelope back">
  <svg class="art" viewBox="0 0 431 208" preserveAspectRatio="none" aria-hidden="true">
    <path d="M0 0 L431 0 L431 40 C431 56 420 64 404 64 L28 64 C12 64 0 56 0 40Z" fill="var(--blue)"/>
  </svg>
  <div class="web">www.silvercreekcm.com</div>
</section>

</body>
</html>
```